Business Card Design Project

Looking to update our business cards. We have a logo with our slogan. We are an IT firm so we wouldlike a modern look.

Industry/Entity Type

Business

```html
<!DOCTYPE html>
<html lang="en">
<head>
<meta charset="utf-8">
<title>Nexora Business Cards</title>
<link rel="stylesheet" href="https://fonts.googleapis.com/css2?family=Jost:wght@400;500;600&display=swap">
<style>
  :root {
    --bg: #e9e6e1;
    --card: #ffffff;
    --green-dark: #687d3b;
    --green-lime: #a9c23f;
    --ink: #2f2f2f;
    --rule: #d4d4d4;
  }
  * { margin: 0; padding: 0; box-sizing: border-box; }
  html, body { width: 1200px; height: 695px; overflow: hidden; }
  body {
    background: var(--bg);
    font-family: "Jost", "Futura", sans-serif;
    color: var(--ink);
    position: relative;
  }
  .card {
    position: absolute;
    width: 540px;
    height: 310px;
    background: var(--card);
    box-shadow: 0 6px 18px rgba(0,0,0,.18);
    overflow: hidden;
  }
  .card--front { left: 50px; top: 90px; }
  .card--back  { left: 610px; top: 295px; }

  /* front */
  .brand {
    position: absolute;
    left: 30px; top: 104px;
    width: 260px;
    text-align: center;
    color: var(--green-dark);
  }
  .brand__name {
    font-size: 50px;
    font-weight: 500;
    letter-spacing: 6px;
    line-height: 1;
  }
  .brand__slogan {
    margin-top: 8px;
    font-size: 11px;
    font-weight: 500;
    letter-spacing: 2.4px;
    white-space: nowrap;
  }
  .divider {
    position: absolute;
    left: 300px; top: 24px;
    width: 1px; height: 196px;
    background: var(--rule);
  }
  .contact {
    position: absolute;
    left: 318px; top: 26px;
  }
  .contact__name {
    font-size: 21px;
    font-weight: 600;
    color: var(--green-dark);
    line-height: 1.1;
  }
  .contact__title {
    font-size: 14px;
    color: var(--green-lime);
    margin-bottom: 12px;
  }
  .contact__list { list-style: none; font-size: 13px; }
  .contact__item {
    display: flex;
    align-items: flex-start;
    gap: 8px;
    line-height: 1.25;
    margin-bottom: 4px;
  }
  .contact__item--address { margin-top: 10px; }
  .contact__icon { width: 11px; height: 11px; margin-top: 3px; flex: none; fill: var(--green-dark); }
  .band-line {
    position: absolute;
    left: 0; right: 0; top: 248px;
    height: 3px;
    background: var(--green-lime);
  }
  .band {
    position: absolute;
    left: 0; right: 0; top: 256px; bottom: 0;
    background: var(--green-dark);
  }
  .band__dot {
    position: absolute;
    left: 250px; top: 226px;
    width: 44px; height: 44px;
    border-radius: 50%;
    background: var(--card);
    border: 5px solid var(--green-dark);
  }

  /* back */
  .back-brand {
    position: absolute;
    left: 0; right: 0; top: 70px;
    text-align: center;
    color: var(--green-dark);
  }
  .back-brand__name {
    font-size: 78px;
    font-weight: 500;
    letter-spacing: 10px;
    line-height: 1;
  }
  .back-brand__slogan {
    margin-top: 10px;
    font-size: 16px;
    font-weight: 500;
    letter-spacing: 3.4px;
  }
  .back-web {
    position: absolute;
    left: 0; right: 0; bottom: 42px;
    text-align: center;
    font-size: 26px;
    letter-spacing: 4px;
    color: var(--ink);
  }
</style>
</head>
<body>

<section class="card card--front" aria-label="Business card front">
  <div class="brand">
    <div class="brand__name">NEXORA</div>
    <div class="brand__slogan">MAKING TECHNOLOGY EASY</div>
  </div>

  <div class="divider"></div>

  <div class="contact">
    <div class="contact__name">Your Name</div>
    <div class="contact__title">Title</div>
    <ul class="contact__list">
      <li class="contact__item">
        <svg class="contact__icon" viewBox="0 0 12 12"><path d="M2.5 0.8 L4.6 0.4 L5.4 3.2 L4 4.2 Q5 6.8 7.8 8 L8.8 6.6 L11.6 7.4 L11.2 9.5 Q10.5 11.6 8 11 Q2 9 1 4 Q0.6 1.6 2.5 0.8Z"/></svg>
        <span>0912 345678</span>
      </li>
      <li class="contact__item">
        <svg class="contact__icon" viewBox="0 0 12 12"><rect x="3" y="0.5" width="6" height="11" rx="1.2"/><rect x="4" y="2" width="4" height="6.5" fill="#fff"/></svg>
        <span>0912 345678</span>
      </li>
      <li class="contact__item">
        <svg class="contact__icon" viewBox="0 0 12 12"><rect x="0.5" y="2.5" width="11" height="7.5" rx="1"/><path d="M1 3 L6 7 L11 3" fill="none" stroke="#fff" stroke-width="1"/></svg>
        <span>info@nexora.com</span>
      </li>
      <li class="contact__item">
        <svg class="contact__icon" viewBox="0 0 12 12"><circle cx="6" cy="6" r="5.5"/><path d="M0.5 6 H11.5 M6 0.5 V11.5 M6 0.5 Q2.5 6 6 11.5 M6 0.5 Q9.5 6 6 11.5" fill="none" stroke="#fff" stroke-width="0.8"/></svg>
        <span>www.nexora.com</span>
      </li>
      <li class="contact__item contact__item--address">
        <svg class="contact__icon" viewBox="0 0 12 12"><path d="M6 0.5 A4 4 0 0 1 10 4.5 Q10 7.5 6 11.5 Q2 7.5 2 4.5 A4 4 0 0 1 6 0.5Z"/><circle cx="6" cy="4.5" r="1.5" fill="#fff"/></svg>
        <span>00, Complex name<br>City, State 0042</span>
      </li>
    </ul>
  </div>

  <div class="band-line"></div>
  <div class="band"></div>
  <div class="band__dot"></div>
</section>

<section class="card card--back" aria-label="Business card back">
  <div class="back-brand">
    <div class="back-brand__name">NEXORA</div>
    <div class="back-brand__slogan">MAKING TECHNOLOGY EASY</div>
  </div>
  <div class="back-web">www.nexora.com</div>
</section>

</body>
</html>
```